Dunmore Roofing

Want a professional looking business card

Industry/Entity Type

Business

Contact Information for Business Card

Paul Dunmore ( Owner) paul@dunmoreroofing-example.com, www.dunmoreroofing-example.com, Adress: 4172 Township road 43 Plantagenet,ON K9X4T2

```html
<!DOCTYPE html>
<html lang="en">
<head>
<meta charset="utf-8">
<title>Dunmore Roofing – Business Card</title>
<link rel="stylesheet" href="https://fonts.googleapis.com/css2?family=Roboto:wght@400;500;700&display=swap">
<style>
  :root {
    --brand-blue: #1d4785;
    --divider-grey: #8a8c92;
    --text-grey: #7b7b7e;
    --paper: #ffffff;
    --backdrop: #2b2b2b;
  }
  * { box-sizing: border-box; margin: 0; padding: 0; }
  html, body {
    width: 1189px; height: 1200px; overflow: hidden;
    background: var(--backdrop);
    font-family: "Roboto", Arial, sans-serif;
  }
  .card {
    position: absolute; left: 171px;
    width: 856px; height: 489px;
    border-radius: 34px; overflow: hidden;
    background: var(--paper);
  }
  .card--front { top: 66px; }
  .card--back { top: 625px; }

  .panel { position: absolute; top: 0; bottom: 0; }
  .card--front .panel--brand { left: 0; width: 423px; background: var(--paper); }
  .card--front .panel--info { left: 427px; right: 0; background: var(--brand-blue); color: var(--paper); }
  .card--back .panel--brand { left: 0; width: 430px; background: var(--brand-blue); }
  .card--back .panel--info { left: 434px; right: 0; background: var(--paper); }
  .divider { position: absolute; top: 0; bottom: 0; width: 4px; background: var(--divider-grey); }
  .card--front .divider { left: 423px; }
  .card--back .divider { left: 430px; }

  .wordmark {
    position: absolute; left: 0; right: 0; top: 244px;
    transform: translateY(-50%);
    display: flex; align-items: center; justify-content: center; gap: 14px;
    font-weight: 700; font-size: 34px; letter-spacing: 1px;
    text-transform: uppercase;
    color: var(--brand-blue);
  }
  .wordmark__square { width: 22px; height: 22px; background: currentColor; }
  .card--back .wordmark { color: var(--paper); }

  .line {
    position: absolute; left: 0; right: 0;
    text-align: center; white-space: nowrap;
    transform: translateY(-50%);
  }
  .contact__name { top: 91px; font-size: 32px; font-weight: 500; }
  .contact__role { top: 116px; font-size: 20px; }
  .contact__icon {
    position: absolute; left: 50%; width: 24px; height: 24px;
    margin-left: -12px; transform: translateY(-50%);
  }
  .contact__icon--phone { top: 171px; }
  .contact__icon--mail { top: 243px; }
  .contact__phone { top: 200px; font-size: 23px; }
  .contact__email { top: 271px; font-size: 21px; }
  .contact__rule {
    position: absolute; left: 50%; width: 265px; margin-left: -132px; height: 1px;
    background: linear-gradient(90deg, transparent, rgba(255,255,255,.85), transparent);
  }
  .contact__rule--one { top: 222px; }
  .contact__rule--two { top: 293px; }
  .contact__address { top: 321px; font-size: 23px; }
  .contact__address--city { top: 349px; }
  .contact__web { top: 399px; font-size: 19px; letter-spacing: 1.4px; }
  .contact__web strong { font-weight: 700; }

  .visit__headline { top: 98px; font-size: 25px; font-weight: 700; color: var(--brand-blue); }
  .visit__copy { font-size: 21px; color: var(--text-grey); }
  .visit__copy--1 { top: 155px; }
  .visit__copy--2 { top: 184px; }
  .visit__copy--3 { top: 213px; }
  .hours { font-size: 21px; color: var(--text-grey); }
  .hours b { font-weight: 700; color: var(--brand-blue); }
  .hours--weekdays { top: 279px; }
  .hours--saturday { top: 307px; }
  .hours--sunday { top: 336px; }
  .visit__web { top: 391px; font-size: 19px; letter-spacing: 1.4px; color: var(--text-grey); }
  .visit__web span { color: var(--brand-blue); }
</style>
</head>
<body>

<section class="card card--front">
  <div class="panel panel--brand">
    <div class="wordmark"><span class="wordmark__square"></span>Dunmore Roofing</div>
  </div>
  <div class="divider"></div>
  <div class="panel panel--info">
    <p class="line contact__name">Paul Dunmore</p>
    <p class="line contact__role">Owner</p>

    <svg class="contact__icon contact__icon--phone" viewBox="0 0 24 24" fill="none" stroke="#fff" stroke-width="1.6">
      <circle cx="12" cy="12" r="10.8"/>
      <path d="M6.5 10.5c0-2 2.5-3 5.5-3s5.5 1 5.5 3v1h-2.6v-1.4h-5.8v1.4H6.5z" fill="#fff" stroke="none"/>
      <rect x="8" y="11.5" width="8" height="5" rx="1" fill="#fff" stroke="none"/>
    </svg>
    <p class="line contact__phone">(555) 018-4273</p>
    <div class="contact__rule contact__rule--one"></div>

    <svg class="contact__icon contact__icon--mail" viewBox="0 0 24 24" fill="none" stroke="#fff" stroke-width="1.6">
      <circle cx="12" cy="12" r="10.8"/>
      <rect x="6.5" y="8" width="11" height="8" rx="1" fill="#fff" stroke="none"/>
      <path d="M6.8 8.4 12 12.6l5.2-4.2M6.8 15.6l3.6-3.3M17.2 15.6l-3.6-3.3" stroke="#1d4785" stroke-width="1.1"/>
    </svg>
    <p class="line contact__email">paul@dunmoreroofing-example.com</p>
    <div class="contact__rule contact__rule--two"></div>

    <p class="line contact__address">4172 Township road 43</p>
    <p class="line contact__address contact__address--city">Harrowfield, WN K9X4T2</p>
    <p class="line contact__web">www.<strong>dunmoreroofing-example</strong>.com</p>
  </div>
</section>

<section class="card card--back">
  <div class="panel panel--brand">
    <div class="wordmark"><span class="wordmark__square"></span>Dunmore Roofing</div>
  </div>
  <div class="divider"></div>
  <div class="panel panel--info">
    <p class="line visit__headline">Better yet, see us in person!</p>
    <p class="line visit__copy visit__copy--1">We love our customers,</p>
    <p class="line visit__copy visit__copy--2">so feel free to visit during</p>
    <p class="line visit__copy visit__copy--3">normal business hours.</p>
    <p class="line hours hours--weekdays"><b>Monday - Friday :</b> 9am - 5pm</p>
    <p class="line hours hours--saturday"><b>Saturday :</b> By appointment</p>
    <p class="line hours hours--sunday"><b>Sunday :</b> Closed</p>
    <p class="line visit__web">www.<span>dunmoreroofing-example</span>.com</p>
  </div>
</section>

</body>
</html>
```